HearthMile business card and stationary design

We are looking for a simple yet elegant design for our mortgage company business card and stationary.

The card should include:
Name (Marcus Pell)
Title (CEO)
Phone Number (732-555-0182)
Address (48 Birchwell Court, Suite 314, Hazlet, NJ 07730)
Email (email@hearthmile.example)
"NMLS" i.e. (NMLS 61947)
"Company NMLS" (Company NMLS 274615)

Contact Information for Business Card

See above

```html
<!DOCTYPE html>
<html lang="en">
<head>
<meta charset="utf-8">
<title>HearthMile business card</title>
<link rel="stylesheet" href="https://fonts.googleapis.com/css2?family=Montserrat:wght@400;500;600&display=swap">
<style>
  :root {
    --stage: #8b8b89;
    --paper: #fbfbfb;
    --navy: #1a2532;
    --blue: #2a9fe0;
    --ink: #3a3a3a;
    --white: #ffffff;
  }
  * { margin: 0; padding: 0; box-sizing: border-box; }
  html, body { width: 1200px; height: 801px; overflow: hidden; }
  body {
    background: var(--stage);
    font-family: "Montserrat", Arial, sans-serif;
    position: relative;
  }
  .card {
    position: absolute;
    top: 252px;
    width: 525px;
    height: 300px;
    box-shadow: 0 10px 24px rgba(0,0,0,0.25);
    border-bottom: 4px solid var(--blue);
  }
  .card--front { left: 50px; background: var(--paper); }
  .card--back { left: 625px; background: var(--navy); }

  .identity {
    position: absolute;
    left: 40px;
    top: 0; bottom: 0;
    width: 190px;
    display: flex; flex-direction: column; justify-content: center; align-items: flex-end;
    text-align: right;
  }
  .identity__name {
    color: var(--blue);
    font-weight: 600;
    font-size: 22px;
    letter-spacing: 1px;
    text-transform: uppercase;
    white-space: nowrap;
  }
  .identity__title {
    color: var(--ink);
    font-size: 14px;
    letter-spacing: 1px;
    margin-top: 2px;
  }
  .divider {
    position: absolute;
    left: 250px;
    top: 80px;
    width: 1.5px;
    height: 140px;
    background: var(--blue);
  }
  .contact {
    position: absolute;
    left: 272px;
    top: 0; bottom: 0;
    display: flex; flex-direction: column; justify-content: center;
    color: var(--ink);
    font-size: 12.5px;
    line-height: 1.55;
    white-space: nowrap;
  }
  .contact__address { margin-bottom: 4px; }
  .contact__row { display: flex; align-items: center; gap: 7px; }
  .contact__icon { width: 11px; height: 11px; flex: none; }

  .brand {
    position: absolute;
    left: 50px; right: 40px;
    top: 108px;
  }
  .brand__name {
    color: var(--white);
    font-weight: 500;
    font-size: 58px;
    letter-spacing: -1px;
    line-height: 1;
    white-space: nowrap;
  }
  .brand__licenses {
    margin-top: 16px;
    color: var(--white);
    font-size: 13.5px;
    letter-spacing: 1.2px;
    display: flex; align-items: center; gap: 12px;
    white-space: nowrap;
  }
  .brand__sep { width: 1.5px; height: 16px; background: var(--blue); }
</style>
</head>
<body>
  <section class="card card--front">
    <div class="identity">
      <p class="identity__name">Marcus Pell</p>
      <p class="identity__title">CEO</p>
    </div>
    <div class="divider"></div>
    <div class="contact">
      <p class="contact__address">48 Birchwell Court, Suite 314<br>Fairhollow, NJ 07791</p>
      <p class="contact__row">
        <svg class="contact__icon" viewBox="0 0 12 12"><path fill="#2a9fe0" d="M2.5 1 4.5 1 5.2 3.6 4 4.6C4.7 6 6 7.3 7.4 8L8.4 6.8 11 7.5 11 9.5C11 10.3 10.3 11 9.5 11 5 11 1 7 1 2.5 1 1.7 1.7 1 2.5 1Z"/></svg>
        732-555-0182
      </p>
      <p class="contact__row">
        <svg class="contact__icon" viewBox="0 0 12 12"><rect x="0.5" y="2" width="11" height="8" fill="#2a9fe0"/><path d="M0.8 2.4 6 6.6 11.2 2.4" stroke="#fbfbfb" stroke-width="1" fill="none"/></svg>
        email@hearthmile.example
      </p>
      <p class="contact__row">
        <svg class="contact__icon" viewBox="0 0 12 12"><circle cx="6" cy="6" r="5.2" fill="none" stroke="#2a9fe0" stroke-width="1.4"/><path d="M0.8 6H11.2M6 0.8C3.6 3.5 3.6 8.5 6 11.2M6 0.8C8.4 3.5 8.4 8.5 6 11.2" stroke="#2a9fe0" stroke-width="1" fill="none"/></svg>
        www.hearthmile.example
      </p>
    </div>
  </section>

  <section class="card card--back">
    <div class="brand">
      <p class="brand__name">HearthMile</p>
      <p class="brand__licenses">
        <span>NMLS 61947</span>
        <span class="brand__sep"></span>
        <span>Company NMLS 274615</span>
      </p>
    </div>
  </section>
</body>
</html>
```